US company marketing to law enforcement needs brochure design

We have created a new logo and now need to update our printed material. What we really need is a "style" or "template" for how our brochures will look in the future. Enclosed is the brochure draft with the old style and logo. Also enclosed is the new logo. As we are marketing to US law enforcement it is important the the brochure design is strong, powerful and that we are looking experienced and trustworthy. However, we also want to look modern in line with the logo update.

Target Market(s)

Law enforcement

Industry/Entity Type

Marketing

```html
<!DOCTYPE html>
<html lang="en">
<head>
<meta charset="UTF-8">
<title>Steadfast Programs – Brochure Cover</title>
<link href="https://fonts.googleapis.com/css2?family=Lato:wght@400;700&display=swap" rel="stylesheet">
<style>
  :root {
    --navy: #1d3767;
    --sky: #8fb0e0;
    --paper: #f4f4f5;
    --fold: #dcdcdf;
    --grey-text: #8b8b8d;
    --bullet-text: #8e8e90;
    --white: #ffffff;
    --photo-dark: #4a2414;
    --photo-mid: #8a4a26;
    --photo-light: #c4874c;
  }
  * { margin: 0; padding: 0; box-sizing: border-box; }
  html, body {
    width: 1200px; height: 850px; overflow: hidden;
    background: var(--paper);
    font-family: "Lato", Arial, sans-serif;
  }
  .brochure {
    position: relative; width: 1200px; height: 850px;
    background: var(--paper); overflow: hidden;
  }
  .brochure-shapes { position: absolute; inset: 0; }
  .fold-line {
    position: absolute; left: 597px; top: 0; width: 1px; height: 850px;
    background: var(--fold);
  }
  .cover-title {
    position: absolute; left: 53px; top: 30px;
    font-size: 31px; font-weight: 700; color: var(--navy);
    letter-spacing: 0.1px;
  }
  .program-list {
    position: absolute; left: 60px; top: 76px; width: 430px;
    list-style: none; display: flex; flex-wrap: wrap; justify-content: center;
    column-gap: 22px; row-gap: 10px;
    font-size: 19px; font-weight: 700; color: var(--bullet-text);
  }
  .program-list li::before {
    content: ""; display: inline-block; width: 7px; height: 7px;
    border-radius: 50%; background: var(--bullet-text);
    margin-right: 6px; vertical-align: middle; position: relative; top: -2px;
  }
  .brand {
    position: absolute; display: flex; align-items: center; gap: 14px;
    font-weight: 700; white-space: nowrap;
  }
  .brand-dot { border-radius: 50%; flex: none; }
  .brand--front { left: 38px; top: 605px; font-size: 31px; color: var(--white); }
  .brand--front .brand-dot { width: 60px; height: 60px; background: var(--white); }
  .brand--back { left: 620px; top: 760px; font-size: 35px; color: var(--grey-text); }
  .brand--back .brand-dot { width: 72px; height: 72px; background: var(--navy); }
</style>
</head>
<body>
<main class="brochure">
  <svg class="brochure-shapes" width="1200" height="850" viewBox="0 0 1200 850">
    <defs>
      <linearGradient id="courtroomTones" x1="0" y1="0" x2="1" y2="1">
        <stop offset="0" stop-color="var(--photo-mid)"/>
        <stop offset="0.45" stop-color="var(--photo-light)"/>
        <stop offset="1" stop-color="var(--photo-dark)"/>
      </linearGradient>
    </defs>
    <path class="accent-band" fill="var(--sky)"
          d="M0,177 L372,568 Q438,640 392,702 L262,850 L0,850 Z"/>
    <path class="front-panel" fill="var(--navy)"
          d="M0,219 L350,590 Q410,641 368,690 L209,850 L0,850 Z"/>
    <path class="photo-frame" fill="var(--navy)"
          d="M720,0 H1200 V850 H1175 L545,378 Q455,300 515,228 Z"/>
    <path class="photo-area" fill="url(#courtroomTones)" role="img"
          aria-label="Photo of brass scales of justice on a wooden bench in a courtroom"
          d="M765,0 H1200 V812 L565,343 Q490,285 548,238 Z"/>
  </svg>

  <div class="fold-line"></div>

  <h1 class="cover-title">Comprehensive Offender Programs</h1>
  <ul class="program-list">
    <li>Pre Trial</li>
    <li>Diversion</li>
    <li>Deferred Prosecution</li>
    <li>Probation</li>
    <li>Jail Alternative</li>
  </ul>

  <div class="brand brand--front">
    <span class="brand-dot"></span>
    <span class="brand-name">Steadfast Programs</span>
  </div>

  <div class="brand brand--back">
    <span class="brand-dot"></span>
    <span class="brand-name">Steadfast Programs</span>
  </div>
</main>
</body>
</html>
```